New Business Card Design Project LORVANTI-Italy

we are LORVANTI-Italy
our company in the market for 3 years we are luxury cosmetic company and its about time for a facelift :)
i will like to have elegant luxurious and unique business card
that will give the person that get it a unique, luxurious and elegant impression
I'm VERY OPEN FOR NEW IDEAS , even duo i add a few files of things that i see on line and i like them

i add my logo as well
my website is LORVANTI.COM
(if you would like to see the main style that we have)

Target Market(s)

adult that have money :)

Industry/Entity Type

Business

Contact Information for Business Card

Name - Dario Lorvanti
Position - CEO and CO Founder
address - 4817 E Halvern
telephone - 555-384-1926
email - dario@lorvanti.com
fax - 555-384-1926
website - LORVANTI.COM

Colors
000000
959595
fbee3e
ffffff

Requirements
Must have
• big logo in GOLD color
• elegant look
• impressive
Nice to have
• not must but maybe classy pattern background
• not must but maybe emblem
• maybe clear plastic business card
Should not have
• colors
• images

```html
<!DOCTYPE html>
<html lang="en">
<head>
<meta charset="utf-8">
<title>LORVANTI Italy – Business Card</title>
<link rel="stylesheet" href="https://fonts.googleapis.com/css2?family=Cinzel:wght@500&family=Open+Sans:wght@400&display=swap">
<style>
  :root {
    --stage: #0b0b0b;
    --card: #141414;
    --card-edge: #1f1f1f;
    --gold: #d6aa2e;
    --white: #ffffff;
    --grey: #959595;
  }
  * { box-sizing: border-box; margin: 0; padding: 0; }
  html, body { width: 1200px; height: 900px; overflow: hidden; background: var(--stage); }
  .stage {
    width: 1200px; height: 900px;
    display: flex; align-items: center; justify-content: center; gap: 40px;
  }
  .card {
    position: relative;
    width: 540px; height: 309px;
    background:
      repeating-linear-gradient(95deg, rgba(255,255,255,0.012) 0 2px, rgba(0,0,0,0.02) 2px 4px),
      var(--card);
    border: 1px solid var(--card-edge);
    box-shadow: 0 20px 40px rgba(0,0,0,0.6);
  }

  /* Front */
  .holder { position: absolute; left: 40px; top: 34px; }
  .holder-name {
    font-family: "Cinzel", serif; font-weight: 500;
    font-size: 19px; letter-spacing: 1px; color: var(--gold);
  }
  .holder-role {
    font-family: "Open Sans", sans-serif; font-size: 11px;
    color: var(--white); margin-top: 2px;
  }
  .contacts {
    position: absolute; left: 40px; top: 108px; list-style: none;
    font-family: "Open Sans", sans-serif; font-size: 12px; color: var(--white);
  }
  .contacts li { display: flex; align-items: center; gap: 8px; height: 19px; }
  .contacts svg { width: 11px; height: 11px; fill: var(--gold); flex: none; }
  .address {
    position: absolute; left: 40px; top: 198px;
    font-family: "Open Sans", sans-serif; font-size: 12px; color: var(--white);
  }

  .brand {
    position: absolute; right: 40px; bottom: 40px;
    display: flex; flex-direction: column; align-items: center;
  }
  .brand-mark { width: 58px; height: 58px; border: 2px solid var(--gold); border-radius: 50%; margin-bottom: 10px; }
  .brand-name {
    font-family: "Cinzel", serif; font-weight: 500;
    font-size: 34px; letter-spacing: 2px; color: var(--gold); line-height: 1;
  }
  .brand-rule { width: 220px; height: 1px; background: var(--gold); margin: 8px 0 6px; }
  .brand-origin {
    font-family: "Cinzel", serif; font-weight: 500;
    font-size: 12px; letter-spacing: 3px; color: var(--gold);
  }

  /* Back */
  .card-back { display: flex; flex-direction: column; align-items: center; justify-content: center; }
  .emblem { width: 110px; height: 110px; border: 3px solid var(--gold); border-radius: 50%; margin-bottom: 16px; }
  .back-name {
    font-family: "Cinzel", serif; font-weight: 500;
    font-size: 24px; letter-spacing: 3px; color: var(--gold);
  }
</style>
</head>
<body>
<main class="stage">
  <section class="card card-front" aria-label="Business card front">
    <div class="holder">
      <p class="holder-name">DARIO LORVANTI</p>
      <p class="holder-role">CEO and CO Founder</p>
    </div>
    <ul class="contacts">
      <li><svg viewBox="0 0 12 12" aria-hidden="true"><path d="M2.5 0.5l2 2.2-1 1.3c.7 1.6 1.9 2.8 3.5 3.5l1.3-1 2.2 2-1.2 2.2C5 12 0 7 0.3 1.7z"/></svg>555-384-1926</li>
      <li><svg viewBox="0 0 12 12" aria-hidden="true"><path d="M3 0h5v3H3zM1 4h10v6H9V8H3v2H1zM3 9h6v3H3z"/></svg>555-384-1926</li>
      <li><svg viewBox="0 0 12 12" aria-hidden="true"><path d="M0 2h12v1.2L6 7 0 3.2zM0 4.6l6 3.8 6-3.8V10H0z"/></svg>dario@lorvanti.com</li>
      <li><svg viewBox="0 0 12 12" aria-hidden="true"><circle cx="6" cy="6" r="5.5" fill="none" stroke="#d6aa2e" stroke-width="1"/><path d="M0.5 6h11M6 0.5c-3 3-3 8 0 11M6 0.5c3 3 3 8 0 11" fill="none" stroke="#d6aa2e" stroke-width="1"/></svg>www.lorvanti.com</li>
    </ul>
    <p class="address">4817 E Halvern</p>
    <div class="brand">
      <span class="brand-mark" aria-hidden="true"></span>
      <p class="brand-name">LORVANTI</p>
      <span class="brand-rule" aria-hidden="true"></span>
      <p class="brand-origin">ITALY</p>
    </div>
  </section>

  <section class="card card-back" aria-label="Business card back">
    <span class="emblem" aria-hidden="true"></span>
    <p class="back-name">LORVANTI</p>
  </section>
</main>
</body>
</html>
```